Wedding Invitation for a wedding at home - personal, romantic event

Want a wedding invitation that is to be printed onto card.
Size to be 148mm x 210mm
For it to open like a book not tent card
Have a picture of a house that I want to be the front cover.
I've attached 2 pictures. I like the picture without the man but with the grass
For the photo to become a drawing and the colours to be brighter.
If you could use the picture of us and get us in one of the windows.
If you could put the picture of the dog maybe somewhere on the grass.
Love the colour of the sky in the picture of the beach

Words to be on the inside of the card:
Together with our families
You are invited to the Wedding Reception of Tessa Pimble and Roy Fenwick
On Saturday 16th of September 2017 at 6pm
At Fenwick's Keep, 41b, Marrow Crescent, Ashcombe, Hollinshire, RH19 4PW
Carriages at 1am
RSVP by Friday 28th of July to 07713 586 201

Words on the Back page:
With all that we have, we've been truly blessed.
Your presence and prayers are all that we request.
But if you desire to give nonetheless,
Monetary gift is one we suggest.

If the pages can be white.
Writing in gold
gold border on all pages

Target Market(s)

Wedding guests

Industry/Entity Type

Wedding

Font styles to use
Script

Requirements
Must have
• Romantic feel. Our wedding colours are white, gold and rose gold.
• Designer to be creative and I do not have much inspiration.
Nice to have
• metallic colours
• Maybe have MR & MRS in gold metallic on the front page

```html
<!DOCTYPE html>
<html lang="en">
<head>
<meta charset="utf-8">
<title>Roy &amp; Tessa – Wedding Reception Invitation</title>
<link rel="stylesheet" href="https://fonts.googleapis.com/css2?family=Great+Vibes&family=Old+Standard+TT:wght@400;700&display=swap">
<style>
  :root {
    --backdrop: #6f6f6f;
    --paper: #ffffff;
    --gold: #a87712;
    --gold-deep: #8c600a;
    --gold-light: #d0a23f;
    --silver: #cfc8bd;
    --sky-top: #9fb7d6;
    --sky-glow: #f4cf86;
    --brick: #b86a4c;
    --lawn: #6d8a45;
    --drive: #c99a82;
  }
  * { margin: 0; padding: 0; box-sizing: border-box; }
  html, body { width: 1200px; height: 613px; overflow: hidden; }
  body {
    background: var(--backdrop);
    position: relative;
    font-family: "Old Standard TT", Georgia, serif;
    color: var(--gold);
  }
  .card {
    position: absolute;
    top: 91px;
    width: 333px;
    height: 471px;
    background: var(--paper);
    overflow: hidden;
  }
  .card--cover { left: 72px; }
  .card--invite { left: 436px; }
  .card--verse { left: 795px; }

  /* Cover */
  .cover-art {
    position: absolute;
    inset: 0;
    background:
      linear-gradient(180deg,
        var(--sky-top) 0%,
        var(--sky-glow) 22%,
        #e9dcc0 34%,
        #7e8a6a 44%,
        var(--brick) 58%,
        #a9684e 74%,
        var(--lawn) 80%,
        var(--drive) 88%,
        #b98d79 100%);
  }
  .cover-frame {
    position: absolute;
    inset: 8px;
    border: 1px solid var(--gold-light);
  }
  .cover-names {
    position: absolute;
    left: 30px;
    top: 30px;
    width: 290px;
    height: 130px;
    font-family: "Great Vibes", cursive;
    font-weight: 400;
    color: var(--gold);
  }
  .cover-names__first {
    position: absolute;
    left: 2px;
    top: 0;
    font-size: 70px;
    line-height: 1;
  }
  .cover-names__amp {
    position: absolute;
    left: 92px;
    top: 20px;
    font-size: 100px;
    line-height: 1;
    color: var(--silver);
  }
  .cover-names__second {
    position: absolute;
    left: 118px;
    top: 56px;
    font-size: 66px;
    line-height: 1;
  }

  /* Inside frames */
  .card-frame {
    position: absolute;
    inset: 20px;
    border: 1.5px solid var(--gold-light);
  }

  /* Invitation page */
  .invite-text {
    position: absolute;
    left: 0;
    width: 100%;
    text-align: center;
    white-space: nowrap;
  }
  .flourish {
    position: absolute;
    left: 50%;
    transform: translateX(-50%);
    height: 2px;
    background: var(--gold);
    border-radius: 2px;
  }
  .flourish--top { top: 50px; width: 162px; }
  .flourish--bottom { top: 426px; width: 108px; }
  .caps {
    font-size: 10px;
    letter-spacing: 0.9px;
    line-height: 17px;
  }
  .couple-name {
    font-size: 20px;
    font-weight: 700;
    letter-spacing: 0.6px;
    color: var(--gold-deep);
  }
  .details {
    font-size: 10.5px;
    line-height: 16px;
  }
  .rsvp {
    font-size: 10.5px;
    line-height: 16px;
  }
  .rsvp strong { font-weight: 700; }

  /* Verse page */
  .verse {
    position: absolute;
    left: 166px;
    top: 240px;
    width: 420px;
    transform: translate(-50%, -50%) rotate(90deg);
    text-align: center;
    white-space: nowrap;
    font-size: 15px;
    line-height: 24px;
    letter-spacing: 0.3px;
    color: var(--gold);
  }
  .verse__initial {
    font-family: "Great Vibes", cursive;
    font-size: 40px;
    line-height: 0;
    vertical-align: -3px;
  }
</style>
</head>
<body>

  <section class="card card--cover" aria-label="Front cover">
    <div class="cover-art" role="img" aria-label="Illustrated red-brick house under a golden sunset sky, with lawn, a paved drive and the couple's dog on the grass"></div>
    <div class="cover-frame"></div>
    <h1 class="cover-names">
      <span class="cover-names__first">Roy</span>
      <span class="cover-names__amp">&amp;</span>
      <span class="cover-names__second">Tessa</span>
    </h1>
  </section>

  <section class="card card--invite" aria-label="Invitation">
    <div class="card-frame"></div>
    <div class="flourish flourish--top" role="img" aria-label="Gold ornamental divider"></div>

    <p class="invite-text caps" style="top:89px;">TOGETHER WITH OUR FAMILIES</p>
    <p class="invite-text caps" style="top:119px;">YOU ARE INVITED TO<br>THE WEDDING RECEPTION OF</p>
    <p class="invite-text couple-name" style="top:162px;">TESSA PIMBLE</p>
    <p class="invite-text caps" style="top:199px;">- AND -</p>
    <p class="invite-text couple-name" style="top:225px;">ROY FENWICK</p>
    <p class="invite-text details" style="top:280px;">
      On Saturday 16th of September 2017 at 6pm<br>
      at Fenwick's Keep, 41b, Marrow Crescent,<br>
      Ashcombe, Hollinshire, RH19 4PW<br>
      Carriages at 1am
    </p>
    <p class="invite-text rsvp" style="top:359px;">
      RSVP by Friday 28th of July<br>
      <strong>to 07713 586 201</strong>
    </p>

    <div class="flourish flourish--bottom" role="img" aria-label="Gold ornamental divider"></div>
  </section>

  <section class="card card--verse" aria-label="Back page">
    <div class="card-frame"></div>
    <p class="verse">
      <span class="verse__initial">W</span>ith all that we have, we've been truly blessed.<br>
      Your presence and prayers are all that we request.<br>
      But if you desire to give nonetheless,<br>
      Monetary gift is one we suggest.
    </p>
  </section>

</body>
</html>
```